Pizza Coupon App Design Project

*******This project will have a guaranteed payout once I see that there is quality work being designed*********

I require the design (no coding) of 4 vertical screens (the screen will not change for horizontal orientation) for Zentrix and Orbalis. The highest res should be used so it can be scaled for older generation phones.

The mobile app will be used to access pizza coupons.

I do not have a specific style or look that I am going for, although I do not want a childish design (e.g. comic sans). The main requirements are for it to be very easy for users to understand and navigate and to be clean and professional.

I am happy if you only produce a design of the main and store selection screens to which I will give feedback before continuing to design the remaining screens.

The selected artist must be flexible in adapting the final design slightly after the contest is completed, during the app development process (maybe a few small modifications over a month or so).
Please do not include any copyrighted images in your deliverables. I must be the sole owner of the graphics once I have paid for them.

I have included attachments which show the process flow and the screen requirements so that will give you the detail you need to design them. I have also included the logo to assist you in your design., *******This project is now guaranteed *********

I have included attachments which show the process flow and the screen requirements so that will give you the detail you need to design them. I have also included the logo to assist you in your design., *******This project will have a guaranteed payout once I see that there is quality work being designed*********

I have included attachments which show the process flow and the screen requirements so that will give you the detail you need to design them. I have also included the logo to assist you in your design.

Reason: Still looking for the perfect design! ******Project is now guaranteed******

******Project is now guaranteed******

Reason: Starting to get some great designs, we are getting much closer! Keep it up.

Target Market(s)

students and 18-30 year olds - People who want cheap meals and people who order pizza online., students and 18-30 year olds - People who want cheap meals and people who order pizza online., students and 18-30 year olds - People who want cheap meals and people who order pizza online.

Industry/Entity Type

Store

Requirements
Must have
• Must have requirements are listed in the attached documents., Must have requirements are listed in the attached documents., Must have requirements are listed in the attached documents.

```html
<!DOCTYPE html>
<html lang="en">
<head>
<meta charset="utf-8">
<title>Select Your Store</title>
<link href="https://fonts.googleapis.com/css2?family=Arimo:wght@400;700&display=swap" rel="stylesheet">
<style>
  :root{
    --page:#e9e7e4;
    --wood-dark:#3a2418;
    --wood-mid:#5a3a26;
    --wood-light:#6e4a31;
    --paper:#f7f5f1;
    --paper-edge:#e4e0d8;
    --accent-orange:#f0962a;
    --accent-red:#c8102e;
    --text-grey:#9a9a9a;
    --text-dark:#3c3c3c;
    --card-top:#ffffff;
    --card-bottom:#e6e6e6;
    --status-bg:rgba(20,12,8,.55);
    --status-text:#ffffff;
  }
  *{box-sizing:border-box;margin:0;padding:0}
  html,body{width:1200px;height:1040px;overflow:hidden;background:var(--page)}
  body{position:relative;font-family:"Arimo",Helvetica,Arial,sans-serif}

  .app-screen{
    position:absolute;left:328px;top:37px;
    width:320px;height:568px;
    transform:scale(1.7);transform-origin:0 0;
    overflow:hidden;
    box-shadow:0 4px 14px rgba(0,0,0,.18);
  }
  .wood-backdrop{
    position:absolute;inset:0;
    background:
      linear-gradient(90deg,
        var(--wood-mid) 0 20%, var(--wood-dark) 20% 21%,
        var(--wood-light) 21% 46%, var(--wood-dark) 46% 47%,
        var(--wood-mid) 47% 73%, var(--wood-dark) 73% 74%,
        var(--wood-light) 74% 100%);
  }

  .status-bar{
    position:absolute;left:0;top:0;width:320px;height:17px;
    background:var(--status-bg);color:var(--status-text);
    font-size:9px;font-weight:700;
    display:flex;align-items:center;justify-content:space-between;padding:0 5px;
  }
  .status-bar .carrier{display:flex;align-items:center;gap:3px}
  .status-bar .clock{position:absolute;left:0;right:0;text-align:center;pointer-events:none}
  .status-bar .indicators{display:flex;align-items:center;gap:4px}

  .header-sheet{
    position:absolute;left:6px;top:19px;width:308px;height:120px;
    background:linear-gradient(180deg,var(--paper),var(--paper-edge));
    border-radius:2px;
    box-shadow:0 2px 4px rgba(0,0,0,.35);
  }
  .header-sheet::after{
    content:"";position:absolute;right:0;top:0;width:52px;height:40px;
    background:linear-gradient(225deg,var(--wood-mid) 0 48%,#d9d4ca 50%,var(--paper) 70%);
  }
  .screen-title{
    position:absolute;left:12px;top:32px;
    font-size:19px;font-weight:700;color:var(--accent-orange);letter-spacing:-.3px;
  }
  .search-field{
    position:absolute;left:14px;top:78px;width:282px;height:33px;
    border-radius:17px;background:#fff;
    border:1px solid #cfcac2;box-shadow:inset 0 1px 3px rgba(0,0,0,.18);
    display:flex;align-items:center;padding:0 8px;gap:6px;
    font-size:13px;color:var(--text-grey);
  }
  .search-field .query{flex:1;display:flex;align-items:center}
  .search-field .caret{display:inline-block;width:1.5px;height:15px;background:var(--accent-red);margin-left:1px}

  .store-list{position:absolute;left:9px;top:150px;width:300px;list-style:none}
  .store-card{
    height:70px;margin-bottom:10px;
    background:linear-gradient(180deg,var(--card-top),var(--card-bottom));
    border-radius:2px;box-shadow:0 1px 3px rgba(0,0,0,.45);
    display:flex;align-items:center;padding:3px;gap:10px;
  }
  .store-photo{width:64px;height:64px;border-radius:2px;flex:none}
  .store-photo.margherita{background:radial-gradient(circle at 45% 50%,#d9442b,#b8752f 60%,#e7d2a8)}
  .store-photo.pasta{background:radial-gradient(circle at 50% 55%,#f2c36b,#c9803b 60%,#efe4cc)}
  .store-name{font-size:18px;color:var(--text-grey);line-height:1.1;margin-bottom:4px}
  .store-name .match{color:var(--accent-red)}
  .store-meta{font-size:8.5px;color:var(--text-dark);line-height:1.3}
  .store-meta strong{font-weight:700}
</style>
</head>
<body>
  <main class="app-screen">
    <div class="wood-backdrop" role="img" aria-label="Dark wooden plank background"></div>

    <div class="status-bar">
      <span class="carrier">
        <svg width="14" height="8" viewBox="0 0 14 8" aria-hidden="true">
          <rect x="0" y="6" width="2" height="2" fill="#fff"/><rect x="3" y="4.5" width="2" height="3.5" fill="#fff"/>
          <rect x="6" y="3" width="2" height="5" fill="#fff"/><rect x="9" y="1.5" width="2" height="6.5" fill="#fff"/>
          <rect x="12" y="0" width="2" height="8" fill="#fff"/>
        </svg>Nordel
      </span>
      <span class="clock">4:20 PM</span>
      <span class="indicators">
        <svg width="8" height="8" viewBox="0 0 8 8" aria-hidden="true"><circle cx="4" cy="4" r="3.5" fill="#fff"/></svg>
        <svg width="8" height="8" viewBox="0 0 8 8" aria-hidden="true"><path d="M8 0 0 3.5 3.5 4.5 4.5 8Z" fill="#fff"/></svg>
        <svg width="8" height="8" viewBox="0 0 8 8" aria-hidden="true"><circle cx="4" cy="4" r="3.2" fill="none" stroke="#fff" stroke-width="1.2"/></svg>
        <svg width="20" height="9" viewBox="0 0 20 9" aria-hidden="true">
          <rect x=".5" y=".5" width="17" height="8" rx="1.5" fill="none" stroke="#fff"/>
          <rect x="2" y="2" width="14" height="5" fill="#fff"/><rect x="18" y="3" width="1.5" height="3" fill="#fff"/>
        </svg>
      </span>
    </div>

    <header class="header-sheet">
      <h1 class="screen-title">Select Your Store</h1>
      <div class="search-field">
        <svg width="12" height="12" viewBox="0 0 12 12" aria-hidden="true">
          <circle cx="5" cy="5" r="3.8" fill="none" stroke="#555" stroke-width="1.5"/>
          <path d="M7.8 7.8 11 11" stroke="#555" stroke-width="1.6" stroke-linecap="round"/>
        </svg>
        <span class="query">Pizza Pa<span class="caret"></span></span>
        <svg width="15" height="15" viewBox="0 0 15 15" aria-hidden="true">
          <circle cx="7.5" cy="7.5" r="7" fill="#9b9b9b"/>
          <path d="M5 5 10 10M10 5 5 10" stroke="#fff" stroke-width="1.6" stroke-linecap="round"/>
        </svg>
      </div>
    </header>

    <ul class="store-list">
      <li class="store-card">
        <div class="store-photo margherita" role="img" aria-label="Photo of a pizza with tomato and basil"></div>
        <div><p class="store-name"><span class="match">Pizza Pa</span>rlor</p>
          <p class="store-meta"><strong>North Elm Street | Cedar Falls</strong><br>WI 54210 | 715-555-0142<br><strong>OPEN DAILY</strong> 11am - 10pm</p></div>
      </li>
      <li class="store-card">
        <div class="store-photo pasta" role="img" aria-label="Photo of a pizza slice with olives"></div>
        <div><p class="store-name"><span class="match">Pizza</span> &amp; <span class="match">Pa</span>sta Corner</p>
          <p class="store-meta"><strong>48 Harbor St. | Brookdale</strong><br>NY 10412 | (212) 555-0187<br><strong>OPEN DAILY</strong> 11am - 10pm</p></div>
      </li>
      <li class="store-card">
        <div class="store-photo margherita" role="img" aria-label="Photo of a pizza with tomato and basil"></div>
        <div><p class="store-name"><span class="match">Pizza Pa</span>rlor</p>
          <p class="store-meta"><strong>North Elm Street | Cedar Falls</strong><br>WI 54210 | 715-555-0142<br><strong>OPEN DAILY</strong> 11am - 10pm</p></div>
      </li>
      <li class="store-card">
        <div class="store-photo pasta" role="img" aria-label="Photo of a pizza slice with olives"></div>
        <div><p class="store-name"><span class="match">Pizza</span> &amp; <span class="match">Pa</span>sta Corner</p>
          <p class="store-meta"><strong>48 Harbor St. | Brookdale</strong><br>NY 10412 | (212) 555-0187<br><strong>OPEN DAILY</strong> 11am - 10pm</p></div>
      </li>
      <li class="store-card">
        <div class="store-photo margherita" role="img" aria-label="Photo of a pizza with tomato and basil"></div>
        <div><p class="store-name"><span class="match">Pizza Pa</span>rlor</p>
          <p class="store-meta"><strong>North Elm Street | Cedar Falls</strong><br>WI 54210 | 715-555-0142<br><strong>OPEN DAILY</strong> 11am - 10pm</p></div>
      </li>
      <li class="store-card">
        <div class="store-photo pasta" role="img" aria-label="Photo of a pizza slice with olives"></div>
        <div><p class="store-name"><span class="match">Pizza</span> &amp; <span class="match">Pa</span>sta Corner</p>
          <p class="store-meta"><strong>48 Harbor St. | Brookdale</strong><br>NY 10412 | (212) 555-0187<br><strong>OPEN DAILY</strong> 11am - 10pm</p></div>
      </li>
    </ul>
  </main>
</body>
</html>
```